Bramblewood Joinery Website

My client Bramblewood Joinery is looking for a redesign for a Word Press Website. Their current site is at www.bramblewoodjoinery.example They are a custom cabinet company, but also create bathroom, living room, bar and entertainment and bedroom cabinets too. They would like a design that emulates the master craftsman work they do yet a contemporary style.

Their current site was designed using Flash elements.

Target Market(s)

Home owners and builders of high end homes

Industry/Entity Type

Entertainment

Font styles to use
Serif
Decorative

Requirements
Must have
• Must show their work and logo using a contemporary style.
Nice to have
• Sliders that showcase their projects.

```html
<!DOCTYPE html>
<html lang="en">
<head>
<meta charset="utf-8">
<title>Bramblewood Joinery</title>
<link href="https://fonts.googleapis.com/css2?family=PT+Sans:wght@400;700&family=Great+Vibes&display=swap" rel="stylesheet">
<style>
:root{
  --page:#efefed;
  --ink:#1f1f1f;
  --muted:#555;
  --green:#3ab03a;
  --green-text:#35a835;
  --nav-top:#4a4a4a;
  --nav-bottom:#1c1c1c;
  --footer:#1f1f1f;
  --footer-ink:#111;
  --white:#fff;
}
*{box-sizing:border-box;margin:0;padding:0}
html,body{width:768px;height:1200px;overflow:hidden}
body{background:var(--page);font-family:"PT Sans",sans-serif;color:var(--ink);position:relative}
.abs{position:absolute}
.brand-mark{left:53px;top:8px;width:64px;height:64px;border-radius:50%;background:var(--green);border:4px solid var(--white);box-shadow:0 0 0 2px #222;z-index:3}
.brand-name{left:124px;top:24px;font-size:15px;font-weight:700;color:var(--ink);z-index:3}
.top-links{right:34px;top:25px;font-size:9px;color:#555}
.top-links span{margin:0 4px;color:#888}
.main-nav{left:33px;top:59px;width:702px;height:31px;background:linear-gradient(var(--nav-top),var(--nav-bottom));display:flex;align-items:center;padding-left:117px;gap:0}
.main-nav a{color:var(--white);font-size:9.4px;text-decoration:none;margin-right:21px;white-space:nowrap}
.hero{left:33px;top:90px;width:702px;height:270px;background:linear-gradient(135deg,#3a2618 0%,#6b4a30 35%,#c9b79a 55%,#5a3b24 75%,#2d1d12 100%)}
.hero-caption{left:33px;top:308px;width:228px;height:42px;background:rgba(30,20,12,.55);color:var(--white);font-family:"Great Vibes",cursive;font-size:24px;padding:8px 0 0 26px}
.hero-arrow{top:212px;width:28px;height:28px}
.welcome{left:0;width:768px;top:380px;text-align:center;font-size:20px;font-weight:400}
.welcome b{font-weight:400;color:var(--green-text)}
.intro{left:100px;width:568px;top:417px;text-align:center;font-size:8.4px;line-height:17px;color:var(--ink)}
.tile{width:201px;height:172px;box-shadow:0 4px 5px rgba(0,0,0,.35)}
.tile-title{width:201px;text-align:center;font-size:12px}
.see-all{width:201px;text-align:center;font-size:7.5px;color:var(--green-text)}
.footer-band{left:0;top:946px;width:768px;height:254px;background:var(--footer)}
.footer-box{left:33px;top:964px;width:702px;height:191px;background:var(--green);color:var(--footer-ink)}
.footer-box h3{position:absolute;top:17px;font-size:12px;font-weight:700}
.about-text{position:absolute;left:16px;top:49px;width:165px;font-size:7.3px;line-height:14.4px}
.about-text p+p{margin-top:0}
.read-more{position:absolute;left:16px;top:155px;font-size:7px;color:#1d5e1d}
.links{position:absolute;top:46px;list-style:none;font-size:7.5px;line-height:18px}
.links li::before{content:"›";margin-right:10px;font-size:9px}
.contact{position:absolute;left:523px;top:49px;font-size:8.6px;line-height:14.4px}
.copyright{left:33px;top:1173px;font-size:8.6px;color:#bbb}
.social{left:496px;top:1168px;display:flex;gap:3.3px}
.social span{width:20px;height:20px;background:#3a3a3a;border:1px solid #4a4a4a}
</style>
</head>
<body>
<div class="abs brand-mark" aria-hidden="true"></div>
<div class="abs brand-name">Bramblewood Joinery</div>
<div class="abs top-links">Entire Store<span>|</span>About Us<span>|</span>Delivery<span>|</span>FAQs<span>|</span>Contacts</div>

<nav class="abs main-nav">
  <a>Home</a><a>Who We Are</a><a>Getting Started</a><a>Contact Us</a><a>Customer Experience</a><a>Professional</a><a>Portfolio</a><a>Cabinet Hardware</a>
</nav>

<div class="abs hero" role="img" aria-label="Slider photo of a dark wood kitchen with island and bar stools"></div>
<svg class="abs hero-arrow" style="left:40px" viewBox="0 0 28 28"><circle cx="14" cy="14" r="13" fill="none" stroke="#fff" stroke-width="1.2"/><path d="M16 9l-5 5 5 5" fill="none" stroke="#fff" stroke-width="1.6"/></svg>
<svg class="abs hero-arrow" style="left:700px" viewBox="0 0 28 28"><circle cx="14" cy="14" r="13" fill="none" stroke="#fff" stroke-width="1.2"/><path d="M12 9l5 5-5 5" fill="none" stroke="#fff" stroke-width="1.6"/></svg>
<div class="abs hero-caption">You dream it, we'll build it</div>

<h1 class="abs welcome">Welcome To <b>Bramblewood Joinery</b></h1>
<p class="abs intro">At Bramblewood Joinery, we've been designing and manufacturing the Midwest's finest custom cabinets and fixtures since 1966. From single cabinets to room remodels to entire home installations, our expert artisans help turn the house you live in to the home you've always dreamed of</p>

<div class="abs tile" style="left:50px;top:476px;background:linear-gradient(135deg,#e8e4dc,#bdb5a6 50%,#5c4a3a)" role="img" aria-label="White kitchen cabinets with steel fridge"></div>
<div class="abs tile-title" style="left:50px;top:657px">Kitchen Cabinet Design</div>
<div class="abs see-all" style="left:50px;top:677px">See All »</div>

<div class="abs tile" style="left:284px;top:476px;background:linear-gradient(135deg,#f0ece4,#a9a39a 50%,#3b2f28)" role="img" aria-label="Open living room with white cabinets and sofa"></div>
<div class="abs tile-title" style="left:284px;top:657px">Living Room Design</div>
<div class="abs see-all" style="left:284px;top:677px">See All »</div>

<div class="abs tile" style="left:519px;top:476px;background:linear-gradient(180deg,#3a2a22,#e8e0c8 45%,#f2f0ea 75%,#6a4a30)" role="img" aria-label="Bedroom with two beds and dark wood panelling"></div>
<div class="abs tile-title" style="left:519px;top:657px">Bedroom Cabinets Design</div>
<div class="abs see-all" style="left:519px;top:677px">See All »</div>

<div class="abs tile" style="left:50px;top:716px;background:linear-gradient(135deg,#d9cfbc,#2c2a2a 50%,#1e1c1c)" role="img" aria-label="Dark bathroom vanity cabinet"></div>
<div class="abs tile-title" style="left:50px;top:897px">Bathroom Cabinet Design</div>
<div class="abs see-all" style="left:50px;top:917px">See All »</div>

<div class="abs tile" style="left:284px;top:716px;background:linear-gradient(135deg,#e6dcc0,#cfa86a 55%,#8a5a2a)" role="img" aria-label="Entertainment room with dark media cabinet and sofa"></div>
<div class="abs tile-title" style="left:284px;top:897px">Entertainment Room Design</div>
<div class="abs see-all" style="left:284px;top:917px">See All »</div>

<div class="abs tile" style="left:519px;top:716px;background:linear-gradient(135deg,#2a2a2a,#d8d8d4 40%,#c8c6c0 70%,#4a2e1e)" role="img" aria-label="White bar cabinets with built-in oven"></div>
<div class="abs tile-title" style="left:519px;top:897px">Bar Cabinets Design</div>
<div class="abs see-all" style="left:519px;top:917px">See All »</div>

<footer>
  <div class="abs footer-band"></div>
  <div class="abs footer-box">
    <h3 style="left:16px">About Us</h3>
    <div class="about-text">
      <p>Every cabinet we build is measured, cut and fitted by hand in our own shop by makers who care.</p>
      <p>Good joinery lasts for decades and grows richer with every year of daily use.</p>
    </div>
    <div class="read-more">Read More About us</div>

    <h3 style="left:243px">Quick Links</h3>
    <ul class="links" style="left:243px">
      <li>Delivery</li><li>Track your order</li><li>Buy gift cards</li><li>Returns</li><li>What's new</li><li>Products</li><li>Our sites</li>
    </ul>
    <ul class="links" style="left:385px">
      <li>Terms</li><li>Conditions</li><li>About us</li><li>Example</li><li>About us</li><li>Custom</li><li>Account</li>
    </ul>

    <h3 style="left:523px">Contact Us</h3>
    <div class="contact">
      Bramblewood Joinery<br>Owen Hartley<br>4820 Alder Lane<br>Fernvale, MO 64000<br><br>Phone: 555.014.2300<br>Fax: 555.014.7835
    </div>
  </div>
  <div class="abs copyright">© 2014 bramblewoodjoinery. All Rights Reserved.</div>
  <div class="abs social" aria-label="Social links">
    <span></span><span></span><span></span><span></span><span></span><span></span><span></span><span></span><span></span><span></span>
  </div>
</footer>
</body>
</html>
```